Layout for site fence advertising - length approx. 250 cm x 125 cm

The advertising will later be printed on a PVC film and used for events or on sports fields.

Main services :
Your regional contact at
Real estate and business financing
independent insurance advice

```html
<!DOCTYPE html>
<html lang="de">
<head>
<meta charset="utf-8">
<title>Lindner Vermögensberatung – Bauzaunbanner</title>
<link href="https://fonts.googleapis.com/css2?family=Open+Sans:ital,wght@0,400;0,700;0,800;1,400&display=swap" rel="stylesheet">
<style>
  :root {
    --blue: #2b52a8;
    --blue-dark: #1f3f8a;
    --grey-band: #5f5f61;
    --grey-light: #e9e9eb;
    --ink: #222226;
    --white: #ffffff;
    --page: #f2f2f2;
  }
  * { box-sizing: border-box; margin: 0; padding: 0; }
  html, body { width: 1200px; height: 900px; overflow: hidden; background: var(--page); }
  body { font-family: "Open Sans", sans-serif; color: var(--ink); }

  .banner {
    position: absolute; left: 40px; top: 170px;
    width: 1120px; height: 560px;
    background: linear-gradient(100deg, var(--white) 45%, var(--grey-light) 100%);
    overflow: hidden;
    box-shadow: 0 4px 18px rgba(0,0,0,.15);
  }
  .banner-shapes { position: absolute; inset: 0; }

  .headline { position: absolute; left: 30px; top: 40px; line-height: 1; }
  .headline .intro { font-size: 38px; font-style: italic; font-weight: 400; color: var(--ink); display: block; }
  .headline .line-two { display: block; margin-top: 14px; font-size: 40px; }
  .headline .line-two strong { font-size: 56px; font-weight: 800; color: var(--blue); }
  .headline .line-three { display: block; margin-top: 6px; font-size: 64px; font-weight: 800; color: var(--blue); letter-spacing: -0.5px; }

  .services { position: absolute; left: 20px; top: 285px; display: flex; align-items: flex-start; }
  .service { display: flex; flex-direction: column; align-items: center; text-align: center; font-size: 19px; line-height: 1.25; }
  .service svg { width: 64px; height: 64px; margin-bottom: 12px; }
  .service-estate { width: 120px; }
  .service-finance { width: 190px; }
  .service-insurance { width: 240px; }
  .divider { width: 2px; height: 130px; background: var(--ink); opacity: .8; margin: 10px 10px 0; }

  .brand { position: absolute; left: 640px; top: 30px; display: flex; align-items: center; gap: 16px; }
  .brand-mark { width: 64px; height: 64px; border-radius: 50%; border: 5px solid var(--blue); }
  .brand-rule { width: 3px; height: 100px; background: var(--ink); }
  .brand-text { font-weight: 700; color: var(--blue); line-height: 1.2; }
  .brand-name { font-size: 24px; }
  .brand-tagline { font-size: 17px; color: var(--ink); font-weight: 400; }

  .portrait {
    position: absolute; left: 830px; top: 130px; width: 270px; height: 430px;
    background: linear-gradient(180deg, #b89a86 0%, #d9bfae 35%, #2d2a33 62%, #1f1c24 100%);
    border-radius: 120px 120px 0 0;
  }

  .contact { position: absolute; left: 0; bottom: 0; height: 80px; width: 780px; display: flex; align-items: center; color: var(--white); }
  .phone { display: flex; align-items: center; gap: 8px; padding-left: 18px; font-size: 42px; font-weight: 700; letter-spacing: -0.5px; }
  .phone svg { width: 20px; height: 34px; }
  .contact-rule { width: 2px; height: 50px; background: var(--white); opacity: .7; margin: 0 30px; }
  .online { font-size: 21px; font-weight: 700; line-height: 1.5; }
  .online div { display: flex; align-items: center; gap: 8px; }
  .online svg { width: 18px; height: 18px; }
</style>
</head>
<body>
<main class="banner">
  <svg class="banner-shapes" viewBox="0 0 1120 560" aria-hidden="true">
    <defs>
      <clipPath id="ringClip"><rect x="770" y="120" width="350" height="440"/></clipPath>
    </defs>
    <g clip-path="url(#ringClip)">
      <circle cx="985" cy="420" r="235" fill="var(--blue)"/>
      <circle cx="985" cy="420" r="205" fill="var(--white)"/>
      <circle cx="995" cy="420" r="195" fill="var(--blue)"/>
      <circle cx="1000" cy="425" r="175" fill="var(--grey-light)"/>
    </g>
    <path d="M0,455 C300,515 600,505 790,330 L800,560 L0,560 Z" fill="var(--grey-band)"/>
    <path d="M0,452 C300,500 620,485 790,328 C620,470 300,490 0,440 Z" fill="var(--white)"/>
    <path d="M70,478 C360,520 640,470 790,338" fill="none" stroke="var(--blue)" stroke-width="9" stroke-linecap="round"/>
  </svg>

  <h1 class="headline">
    <span class="intro">Ihr regionaler</span>
    <span class="line-two"><strong>Finanz</strong>- und</span>
    <span class="line-three">Versicherungsexperte</span>
  </h1>

  <section class="services">
    <div class="service service-estate">
      <svg viewBox="0 0 64 64"><circle cx="32" cy="32" r="29" fill="var(--white)" stroke="var(--blue)" stroke-width="3"/><path d="M16 33 L32 19 L48 33 M21 30 V45 H43 V30" fill="none" stroke="var(--grey-band)" stroke-width="4" stroke-linejoin="round"/><rect x="28" y="35" width="8" height="10" fill="var(--grey-band)"/></svg>
      <span>Real<br>Estate</span>
    </div>
    <div class="divider"></div>
    <div class="service service-finance">
      <svg viewBox="0 0 64 64"><circle cx="32" cy="32" r="29" fill="var(--white)" stroke="var(--blue)" stroke-width="3"/><circle cx="32" cy="34" r="14" fill="var(--grey-band)"/><text x="32" y="41" text-anchor="middle" font-family="Open Sans, sans-serif" font-size="18" font-weight="700" fill="var(--white)">$</text></svg>
      <span>Business<br>Financing</span>
    </div>
    <div class="divider"></div>
    <div class="service service-insurance">
      <svg viewBox="0 0 64 64"><circle cx="32" cy="32" r="29" fill="var(--white)" stroke="var(--blue)" stroke-width="3"/><path d="M32 15 L46 20 V31 C46 40 40 46 32 50 C24 46 18 40 18 31 V20 Z" fill="var(--grey-band)"/><path d="M25 32 L30 37 L39 27" fill="none" stroke="var(--white)" stroke-width="3.5" stroke-linecap="round" stroke-linejoin="round"/></svg>
      <span>Independent<br>Insurance Advice</span>
    </div>
  </section>

  <header class="brand">
    <div class="brand-mark"></div>
    <div class="brand-rule"></div>
    <div class="brand-text">
      <div class="brand-name">Lindner Vermögensberatung GmbH</div>
      <div class="brand-tagline">Finanzieren, Versichern, Vorsorgen</div>
    </div>
  </header>

  <div class="portrait" role="img" aria-label="Porträtfoto des Beraters in dunklem Sakko und weißem Hemd"></div>

  <footer class="contact">
    <div class="phone">
      <svg viewBox="0 0 20 34"><rect x="1.5" y="1.5" width="17" height="31" rx="3" fill="none" stroke="var(--white)" stroke-width="2.5"/><circle cx="10" cy="28" r="1.6" fill="var(--white)"/></svg>
      <span>0650/214 5830</span>
    </div>
    <div class="contact-rule"></div>
    <div class="online">
      <div><svg viewBox="0 0 18 18"><circle cx="9" cy="9" r="7.5" fill="none" stroke="var(--white)" stroke-width="1.6"/><ellipse cx="9" cy="9" rx="3.3" ry="7.5" fill="none" stroke="var(--white)" stroke-width="1.4"/><path d="M1.5 9 H16.5" stroke="var(--white)" stroke-width="1.4"/></svg>www.der-lindner.at</div>
      <div><svg viewBox="0 0 18 18"><rect x="1" y="3.5" width="16" height="11" rx="1.5" fill="var(--white)"/><path d="M1.5 4.5 L9 10 L16.5 4.5" fill="none" stroke="var(--grey-band)" stroke-width="1.5"/></svg>office@der-lindner.at</div>
    </div>
  </footer>
</main>
</body>
</html>
```